Brell Stone Company Business Cards

Front and Back Business Card - logo and text setup - cool design. I need workable photoshop or illustrator files so I can setup each employee card with design that is created
Updates

Hi everyone, thank you for the great entries. Please no more white and blue cards - there are so many already - black and silver only now please. thanks!

Target Market(s)

Construction Industry - Facility Managers

Industry/Entity Type

Construction

Contact Information for Business Card

I really like contemporary simplistic looks - clean neat....not opposed to seeing some black backrounds

Requirements
Must have
• Logo/website address with design on front only - www.brellstone-example.com (logo attached)
• Back:
• Name/Title/Company Address/Phone/email address
Nice to have
• Cool design
Should not have
• Nothing gimmicky like Fire or Water - since we are a Fire Protection company - it has all been done

```html
<!DOCTYPE html>
<html lang="en">
<head>
<meta charset="utf-8">
<title>Brell Stone Company Business Cards</title>
<link rel="stylesheet" href="https://fonts.googleapis.com/css2?family=Lato:ital,wght@0,400;0,700;0,900;1,400&display=swap">
<style>
  :root {
    --bg: #5c5c5e;
    --card-dark: #2f2f31;
    --card-black: #1f1f21;
    --emboss: #3a3a3d;
    --silver: #c7c9cc;
    --silver-light: #e4e5e7;
    --silver-mid: #9a9ca0;
    --steel: #6e7074;
    --text-soft: #b3b5b8;
  }
  * { margin: 0; padding: 0; box-sizing: border-box; }
  html, body { width: 1200px; height: 1126px; overflow: hidden; }
  body {
    background: var(--bg);
    font-family: "Lato", sans-serif;
    position: relative;
  }
  .card {
    position: absolute;
    left: 180px;
    width: 840px;
    height: 480px;
    overflow: hidden;
    box-shadow: 0 8px 24px rgba(0,0,0,0.35);
  }
  /* Front */
  .card-front { top: 50px; background: var(--card-dark); }
  .front-name {
    position: absolute;
    top: 150px; left: 0; right: 0;
    text-align: center;
    font-weight: 900;
    font-size: 92px;
    letter-spacing: -1px;
    color: var(--emboss);
  }
  .front-web {
    position: absolute;
    top: 330px; left: 80px; right: 80px;
    display: flex; align-items: center; gap: 18px;
  }
  .front-web .rule { flex: 1; height: 1px; background: var(--silver); }
  .front-web span {
    color: var(--silver-light); font-size: 18px; letter-spacing: 4px; font-weight: 700;
  }
  /* Back */
  .card-back { top: 590px; background: var(--card-black); }
  .back-name {
    position: absolute;
    top: 48px; left: 52px;
    font-weight: 900;
    font-size: 62px;
    letter-spacing: -1px;
    color: var(--silver);
  }
  .person {
    position: absolute;
    top: 160px; right: 80px;
    text-align: right;
    line-height: 1.2;
  }
  .person .name { color: var(--silver-light); font-weight: 700; font-size: 29px; }
  .person .title { color: var(--text-soft); font-size: 22px; }
  .back-rule {
    position: absolute;
    top: 250px; left: 52px; right: 70px;
    height: 2px; background: var(--steel);
  }
  .contact {
    position: absolute;
    top: 272px; left: 52px;
    color: var(--text-soft);
    font-size: 21px;
    line-height: 1.3;
  }
  .contact .address { font-style: italic; margin-bottom: 8px; }
  .contact .row { display: flex; align-items: center; gap: 12px; }
  .contact svg { width: 16px; height: 16px; }
  .side-tab {
    position: absolute;
    right: 0; top: 168px;
    width: 22px; height: 66px;
    background: var(--silver-mid);
  }
  .bands { position: absolute; left: 0; bottom: 0; width: 840px; height: 60px; }
</style>
</head>
<body>
  <section class="card card-front">
    <div class="front-name">Brell Stone</div>
    <div class="front-web">
      <div class="rule"></div>
      <span>www.brellstone-example.com</span>
      <div class="rule"></div>
    </div>
  </section>

  <section class="card card-back">
    <div class="back-name">Brell Stone</div>
    <div class="person">
      <div class="name">Marcus Delane</div>
      <div class="title">Managing Director</div>
    </div>
    <div class="back-rule"></div>
    <div class="side-tab"></div>
    <div class="contact">
      <div class="address">Co. Street, Suite, Building<br>City/State, Zip Code</div>
      <div class="row">
        <svg viewBox="0 0 16 16" aria-hidden="true"><path d="M3 1.5l3 3-1.5 2a9 9 0 0 0 5 5l2-1.5 3 3-2 2C6 14.5 1.5 10 1 3z" fill="none" stroke="#c7c9cc" stroke-width="1.4"/></svg>
        <span>300.555.0142</span>
      </div>
      <div class="row">
        <svg viewBox="0 0 16 16" aria-hidden="true"><rect x="1" y="3" width="14" height="10" fill="none" stroke="#c7c9cc" stroke-width="1.4"/><path d="M1 3l7 6 7-6" fill="none" stroke="#c7c9cc" stroke-width="1.4"/></svg>
        <span>info@brellstone-example.com</span>
      </div>
    </div>
    <svg class="bands" viewBox="0 0 840 60" aria-hidden="true">
      <polygon points="0,40 560,40 540,60 0,60" fill="#c7c9cc"/>
      <polygon points="580,18 840,18 840,60 550,60" fill="#6e7074"/>
    </svg>
  </section>
</body>
</html>
```